Business card for law firm

Need business card for new law firm. Think confident, authoritative, conservative, but not stuffy or old-fashioned.

Contact Information for Business Card

Content for card - logo (uploaded), plus the following:

Paul Whitcombe (larger font)
Managing Partner (larger font, but not as large as name)
Level 9, 7 Ferris Lane
Sydney NSW 2000
Main Tel 02 9364 2710
Direct Tel 02 8472 3159
Email paul@qvlegal.com.au
www.qvlegal.com.au

Letterhead design should include logo plus:
Level 9, 7 Ferris Lane
Sydney NSW 2000
Tel 02 8472 3159
www.qvlegal.com.au

```html
<!DOCTYPE html>
<html lang="en">
<head>
<meta charset="utf-8">
<title>Quayvale Legal – Business Card</title>
<link href="https://fonts.googleapis.com/css2?family=Open+Sans:wght@400;600;700&display=swap" rel="stylesheet">
<style>
  :root{
    --navy:#001a57;
    --ink:#000000;
    --paper:#ffffff;
    --text:#1b1b1b;
    --rule:#b5b5b5;
    --bg-light:#ececed;
    --bg-dark:#c9cacc;
  }
  *{margin:0;padding:0;box-sizing:border-box}
  html,body{width:1200px;height:1113px;overflow:hidden}
  body{background:linear-gradient(160deg,var(--bg-light) 0%,#dedfe0 55%,var(--bg-dark) 100%);font-family:"Open Sans",Arial,sans-serif}
  .stage{position:absolute;left:0;top:0;width:1242px;height:1152px;transform:scale(.9662);transform-origin:0 0}
  .card{position:absolute;width:794px;height:454px;border-radius:42px;overflow:hidden}
  .card--front{left:58px;top:78px;background:var(--paper);border:1px solid #c4c4c4}
  .card--back{left:354px;top:597px;background:var(--ink)}
  .swoosh{position:absolute;left:0;top:0;width:794px;height:454px}
  .holder{position:absolute;right:34px;top:34px;text-align:right;color:var(--paper)}
  .holder__name{font-weight:700;font-size:30px;line-height:40px;letter-spacing:-.2px}
  .holder__role{font-size:23px;line-height:30px;margin-top:2px}
  .mark-square{position:absolute;background:var(--navy)}
  .card--front .mark-square{left:175px;top:62px;width:72px;height:96px}
  .card--back .mark-square{left:355px;top:79px;width:93px;height:124px;background:var(--paper)}
  .wordmark{position:absolute;left:0;text-align:center;font-weight:400;color:var(--ink)}
  .card--front .wordmark{left:48px;width:320px;top:184px}
  .wordmark__name{display:block;font-size:46px;line-height:56px;letter-spacing:2px}
  .wordmark__sub{display:block;font-size:18px;line-height:24px;letter-spacing:18px;margin-left:18px}
  .card--back .wordmark{width:794px;top:232px;color:var(--paper)}
  .card--back .wordmark__name{font-size:58px;line-height:70px;letter-spacing:3px}
  .card--back .wordmark__sub{font-size:24px;line-height:30px;letter-spacing:26px;margin-left:26px;margin-top:8px}
  .contacts{position:absolute;left:44px;top:295px;list-style:none;color:var(--text);font-size:21px}
  .contacts li{display:flex;align-items:center;height:34px}
  .contacts svg{width:19px;height:19px;margin-right:7px;fill:none;stroke:var(--navy);stroke-width:2}
  .divider{position:absolute;left:309px;top:369px;width:1px;height:54px;background:var(--rule)}
  .address{position:absolute;left:334px;top:368px;color:var(--text);font-size:21px;line-height:31px;font-style:normal}
  .web{position:absolute;left:0;width:794px;top:380px;text-align:center;color:var(--paper);font-size:23px;letter-spacing:4px}
  .web b{font-weight:700}
</style>
</head>
<body>
<div class="stage">
  <section class="card card--front">
    <svg class="swoosh" viewBox="0 0 794 454" preserveAspectRatio="none" aria-hidden="true">
      <path d="M0 80 C260 0 560 130 794 240 L794 272 C560 160 280 20 0 80 Z" fill="var(--ink)"/>
      <path d="M0 72 C270 0 560 125 794 232 L794 248 C560 135 270 10 0 76 Z" fill="var(--paper)"/>
      <path d="M0 0 H794 V234 C560 120 270 -5 0 76 Z" fill="var(--navy)"/>
    </svg>
    <div class="holder">
      <div class="holder__name">PAUL WHITCOMBE</div>
      <div class="holder__role">MANAGING PARTNER</div>
    </div>
    <div class="mark-square" aria-hidden="true"></div>
    <div class="wordmark">
      <span class="wordmark__name">QUAYVALE</span>
      <span class="wordmark__sub">LEGAL</span>
    </div>
    <ul class="contacts">
      <li><svg viewBox="0 0 20 20"><circle cx="10" cy="10" r="8"/><path d="M7 6c-1 3 1 7 5 8l1-2-2-1-1 1c-1-1-2-2-2-3l1-1-1-2z" fill="var(--navy)" stroke="none"/></svg>02 9364 2710(Main)</li>
      <li><svg viewBox="0 0 20 20"><circle cx="10" cy="10" r="8"/><path d="M7 6c-1 3 1 7 5 8l1-2-2-1-1 1c-1-1-2-2-2-3l1-1-1-2z" fill="var(--navy)" stroke="none"/></svg>02 8472 3159(Direct)</li>
      <li><svg viewBox="0 0 20 20"><rect x="2" y="6" width="16" height="11" fill="var(--navy)" stroke="none"/><path d="M2 7l8 6 8-6" stroke="#fff" stroke-width="1.5"/></svg>paul@qvlegal.com.au</li>
      <li><svg viewBox="0 0 20 20" style="stroke-width:1.4"><circle cx="10" cy="10" r="8"/><ellipse cx="10" cy="10" rx="3.5" ry="8"/><path d="M2 10h16M3.5 6h13M3.5 14h13"/></svg>www.qvlegal.com.au</li>
    </ul>
    <div class="divider"></div>
    <address class="address">Level 9, 7 Ferris Lane<br>Sydney NSW 2000</address>
  </section>

  <section class="card card--back">
    <div class="mark-square" aria-hidden="true"></div>
    <div class="wordmark">
      <span class="wordmark__name">QUAYVALE</span>
      <span class="wordmark__sub">LEGAL</span>
    </div>
    <p class="web">www.<b>qvlegal</b>.com.au</p>
  </section>
</div>
</body>
</html>
```